Redesign of Medical App for Patients

• The Designer’s task is to provide a new fully-responsive design for our apps, and then code it using only basic html and CSS.
• Your design will be incorporated into our existing REACT native app.

Target Market(s)

Medical Patients

Industry/Entity Type

Medical

Coding

Coded - Design and coding required

Number of Pages Required

5+ page

Requirements
Must have
• Short list candidates will receive detailed briefing
Nice to have
• detailed briefing contains some of our ideas.

```html
<!DOCTYPE html>
<html lang="en">
<head>
<meta charset="utf-8">
<title>CarePath – Patient Screens</title>
<link href="https://fonts.googleapis.com/css2?family=Exo+2:ital,wght@0,300;0,400;0,500;0,600;0,700;0,800;1,300&display=swap" rel="stylesheet">
<style>
:root{
  --blue:#2585b6;
  --ink:#2e2e2e;
  --text:#4a4a4a;
  --line:#9b9b9b;
  --nav:#333333;
  --nav-icon:#7a7a7a;
  --bg:#999999;
  --white:#ffffff;
}
*{box-sizing:border-box;margin:0;padding:0}
html,body{width:840px;height:1200px;overflow:hidden}
body{background:radial-gradient(ellipse at 50% 20%,#a6a6a6 0%,var(--bg) 70%);font-family:"Exo 2",sans-serif;position:relative;color:var(--ink)}
.screen{position:absolute;top:80px;width:221px;background:var(--white);box-shadow:0 10px 30px rgba(0,0,0,.35);overflow:hidden}
.screen--about{left:65px;height:645px}
.screen--pre{left:310px;height:645px}
.screen--procedure{left:554px;height:1040px}
.brand{position:absolute;top:9px;left:15px;display:flex;align-items:center;gap:7px}
.brand__dot{width:34px;height:34px;border-radius:50%;background:var(--blue)}
.brand__name{font-size:23px;font-weight:500;color:var(--ink);letter-spacing:.3px}
.banner{position:absolute;top:52px;left:0;width:221px;height:64px}
.banner__title{position:absolute;top:52px;left:0;width:221px;height:64px;display:flex;align-items:center;justify-content:center;color:var(--white);font-weight:800;font-size:20px;letter-spacing:.2px}
.accordion{position:absolute;left:12px;width:197px;height:35px;border:1px solid var(--line);background:var(--white);display:flex;align-items:center;padding-left:14px}
.accordion__label{font-size:9.6px;font-weight:600;line-height:10.5px;color:var(--ink);width:140px}
.accordion__toggle{position:absolute;right:5px;top:4px;width:26px;height:26px;background:var(--blue);color:var(--white);display:flex;align-items:center;justify-content:center;font-size:16px;font-weight:700}
.copy{position:absolute;font-size:7.3px;line-height:10.6px;font-weight:400;color:var(--text);text-align:justify}
.copy p{margin-bottom:10.6px}
.copy p.gap{margin-bottom:21px}
.about-copy{left:15px;top:179px;width:192px}
.art{position:absolute}
.art--liver{left:0;top:455px;width:221px;height:156px;background:radial-gradient(ellipse at 45% 60%,#c8283a 0%,#d9545f 28%,#bfe6f5 55%,#e9f7fc 100%)}
.art--patient{left:0;top:390px;width:221px;height:221px;background:radial-gradient(ellipse at 60% 60%,#a9c4e2 0%,#cfdff0 40%,#ffffff 80%)}
.art--surgery{left:13px;top:211px;width:195px;height:177px;border:2px solid #c9ccd0;background:radial-gradient(ellipse at 45% 45%,#2b7a62 0%,#c96a6a 35%,#f1d6d6 60%,#ffffff 85%)}
.nav{position:absolute;left:0;bottom:0;width:221px;height:34px;background:var(--nav)}
.nav svg{position:absolute;top:9px}
.pill{position:absolute;left:10px;width:200px;height:41px;border-radius:21px;display:flex;align-items:center;justify-content:center;font-weight:800;font-size:15px;letter-spacing:.2px}
.pill--active{top:130px;background:var(--nav);color:var(--white)}
.pill--outline{top:177px;border:2px solid var(--blue);color:var(--blue)}
.task-hint{position:absolute;left:12px;top:239px;display:flex;align-items:center;gap:5px;font-size:8.5px;font-style:italic;font-weight:300;color:var(--text)}
.task{position:absolute;left:13px;width:198px;height:14px}
.task__box{position:absolute;left:0;top:2px;width:10px;height:10px;border:1.4px solid var(--ink)}
.task__label{position:absolute;left:23px;top:0;font-size:10.6px;font-weight:700;color:var(--ink);white-space:nowrap}
.task__plus{position:absolute;right:6px;top:0;font-size:10px;font-weight:700}
.task__note{position:absolute;left:36px;top:311px;font-size:5.6px;color:var(--blue)}
.procedure-copy{left:13px;top:405px;width:193px}
</style>
</head>
<body>

<section class="screen screen--about">
  <div class="brand"><span class="brand__dot"></span><span class="brand__name">CAREPATH</span></div>
  <svg class="banner" viewBox="0 0 221 64" aria-hidden="true"><path d="M0 12 Q110 -6 221 12 L221 52 Q110 72 0 52 Z" fill="var(--blue)"/></svg>
  <h1 class="banner__title">ABOUT PROCEDURE</h1>

  <div class="accordion" style="top:131px"><span class="accordion__label">Is it too late to prevent gallbladder disease?</span><span class="accordion__toggle">-</span></div>

  <div class="copy about-copy">
    <p>Yes, unfortunately. If you have symptomatic gallbladder disease, surgery is the most likely solution. Gallstones rarely go away spontaneously.</p>
    <p>It is not entirely understood why some people get gallstones. Probable factors include weight, level of physical activity, pregnancy, certain medications containing estrogen, and diet. For example, sometimes patients will try to decrease the amount of fat they consume to avoid gallbladder attacks.</p>
    <p>There are numerous homeopathic/natural remedies that suggest they can treat gallbladder disease on their own, but these have not been proven scientifically. There are other more proven solutions to eliminate gallstones – if only temporarily – as well as another surgery to do the same. See below.</p>
  </div>

  <div class="art art--liver" role="img" aria-label="Medical illustration of the liver with gallbladder and blood vessels on a light blue background"></div>

  <div class="accordion" style="top:373px"><span class="accordion__label">What will happen if I don’t have this procedure?</span><span class="accordion__toggle">+</span></div>
  <div class="accordion" style="top:415px"><span class="accordion__label">Are there alternative solutions?</span><span class="accordion__toggle">+</span></div>
  <div class="accordion" style="top:458px"><span class="accordion__label">What are the risks of this procedure?</span><span class="accordion__toggle">+</span></div>

  <nav class="nav" aria-label="App navigation">
    <svg style="left:17px" width="16" height="16" viewBox="0 0 16 16"><path d="M1 8 L8 2 L15 8 L13 8 L13 14 L9.5 14 L9.5 10 L6.5 10 L6.5 14 L3 14 L3 8 Z" fill="#fff"/></svg>
    <svg style="left:61px" width="16" height="16" viewBox="0 0 16 16" fill="var(--nav-icon)"><circle cx="8" cy="5" r="2.6"/><circle cx="3" cy="6" r="2"/><circle cx="13" cy="6" r="2"/><path d="M3 14 Q3 8.5 8 8.5 Q13 8.5 13 14 Z"/><path d="M0 13 Q0 9 3 9 L4 9 Q2.5 11 2.5 13 Z M16 13 Q16 9 13 9 L12 9 Q13.5 11 13.5 13 Z"/></svg>
    <svg style="left:103px" width="16" height="16" viewBox="0 0 16 16"><circle cx="8" cy="8" r="7" fill="none" stroke="var(--nav-icon)" stroke-width="1.6"/><path d="M11.5 8 H5 M7.5 5 L4.5 8 L7.5 11" fill="none" stroke="var(--nav-icon)" stroke-width="1.8"/></svg>
    <svg style="left:145px" width="16" height="16" viewBox="0 0 16 16"><circle cx="8" cy="8" r="7" fill="none" stroke="var(--nav-icon)" stroke-width="1.6"/><path d="M4.5 8 H11 M8.5 5 L11.5 8 L8.5 11" fill="none" stroke="var(--nav-icon)" stroke-width="1.8"/></svg>
    <svg style="left:188px" width="16" height="16" viewBox="0 0 16 16"><circle cx="8" cy="8" r="5" fill="none" stroke="var(--nav-icon)" stroke-width="3" stroke-dasharray="2.2 1.7"/><circle cx="8" cy="8" r="4" fill="var(--nav-icon)"/><circle cx="8" cy="8" r="1.6" fill="var(--nav)"/></svg>
  </nav>
</section>

<section class="screen screen--pre">
  <div class="brand"><span class="brand__dot"></span><span class="brand__name">CAREPATH</span></div>
  <svg class="banner" viewBox="0 0 221 64" aria-hidden="true"><path d="M0 12 Q110 -6 221 12 L221 52 Q110 72 0 52 Z" fill="var(--blue)"/></svg>
  <h1 class="banner__title">PRE-PROCEDURE</h1>

  <div class="pill pill--active">WEEKS BEFORE</div>
  <div class="pill pill--outline">DAY BEFORE</div>

  <div class="task-hint">
    <svg width="12" height="12" viewBox="0 0 12 12"><rect x="1" y="2" width="9" height="9" fill="none" stroke="var(--ink)" stroke-width="1.2"/><path d="M3 6 L5.5 8.5 L11 1.5" fill="none" stroke="var(--ink)" stroke-width="1.3"/></svg>
    <span>Check when task is completed</span>
  </div>

  <div class="task" style="top:270px"><span class="task__box"></span><span class="task__label">Pre-operative appointment</span><span class="task__plus">+</span></div>
  <div class="task" style="top:297px"><span class="task__box"></span><span class="task__label">8 weeks before</span><span class="task__plus">+</span></div>
  <span class="task__note">(or after your pre-operative appointment)</span>
  <div class="task" style="top:325px"><span class="task__box"></span><span class="task__label">6 weeks before</span><span class="task__plus">+</span></div>
  <div class="task" style="top:352px"><span class="task__box"></span><span class="task__label">2 weeks before</span><span class="task__plus">+</span></div>
  <div class="task" style="top:379px"><span class="task__box"></span><span class="task__label">1 week before</span><span class="task__plus">+</span></div>

  <div class="art art--patient" role="img" aria-label="Photo of a woman in a light blue sweater holding her lower back in discomfort"></div>

  <nav class="nav" aria-label="App navigation">
    <svg style="left:17px" width="16" height="16" viewBox="0 0 16 16"><path d="M1 8 L8 2 L15 8 L13 8 L13 14 L9.5 14 L9.5 10 L6.5 10 L6.5 14 L3 14 L3 8 Z" fill="#fff"/></svg>
    <svg style="left:61px" width="16" height="16" viewBox="0 0 16 16" fill="var(--nav-icon)"><circle cx="8" cy="5" r="2.6"/><circle cx="3" cy="6" r="2"/><circle cx="13" cy="6" r="2"/><path d="M3 14 Q3 8.5 8 8.5 Q13 8.5 13 14 Z"/><path d="M0 13 Q0 9 3 9 L4 9 Q2.5 11 2.5 13 Z M16 13 Q16 9 13 9 L12 9 Q13.5 11 13.5 13 Z"/></svg>
    <svg style="left:103px" width="16" height="16" viewBox="0 0 16 16"><circle cx="8" cy="8" r="7" fill="none" stroke="var(--nav-icon)" stroke-width="1.6"/><path d="M11.5 8 H5 M7.5 5 L4.5 8 L7.5 11" fill="none" stroke="var(--nav-icon)" stroke-width="1.8"/></svg>
    <svg style="left:145px" width="16" height="16" viewBox="0 0 16 16"><circle cx="8" cy="8" r="7" fill="none" stroke="var(--nav-icon)" stroke-width="1.6"/><path d="M4.5 8 H11 M8.5 5 L11.5 8 L8.5 11" fill="none" stroke="var(--nav-icon)" stroke-width="1.8"/></svg>
    <svg style="left:188px" width="16" height="16" viewBox="0 0 16 16"><circle cx="8" cy="8" r="5" fill="none" stroke="var(--nav-icon)" stroke-width="3" stroke-dasharray="2.2 1.7"/><circle cx="8" cy="8" r="4" fill="var(--nav-icon)"/><circle cx="8" cy="8" r="1.6" fill="var(--nav)"/></svg>
  </nav>
</section>

<section class="screen screen--procedure">
  <div class="brand"><span class="brand__dot"></span><span class="brand__name">CAREPATH</span></div>
  <svg class="banner" viewBox="0 0 221 64" aria-hidden="true"><path d="M0 12 Q110 -6 221 12 L221 52 Q110 72 0 52 Z" fill="var(--blue)"/></svg>
  <h1 class="banner__title">PROCEDURE</h1>

  <div class="accordion" style="top:128px"><span class="accordion__label">Preparation</span><span class="accordion__toggle">+</span></div>
  <div class="accordion" style="top:171px"><span class="accordion__label">What Happens?</span><span class="accordion__toggle">-</span></div>

  <div class="art art--surgery" role="img" aria-label="Medical illustration of laparoscopic instruments removing the gallbladder"></div>

  <div class="copy procedure-copy">
    <p>Just prior to your operation, you will undergo general anesthesia and have a breathing tube, otherwise known as an endotracheal tube, placed down your throat (i.e. intubation). Your breathing tube will most likely be removed by the time you wake up from your surgery.</p>
    <p>Anesthesia will prevent you from feeling or remembering the procedure and will be given to you through your IV. Your endotracheal tube will ensure your lungs receive oxygen during the procedure. A Foley catheter will likely be placed to drain your bladder after you are asleep under general anesthesia. Special boots, known as sequential compression devices, will be placed on your legs to massage them and prevent blood clots.</p>
    <p class="gap">During the procedure your surgeon will make four tiny incisions in your belly. One of these will be around your belly-button and the other three will be just below your ribcage.</p>
    <p>Carbon dioxide will be pumped into your belly to provide your surgeon with the space needed to see inside with a camera, known as a laparoscope, and perform the procedure. The picture from the laparoscope will be shown on screens inside the operating room. The four incisions will allow entry of the camera and instruments your surgeon needs to complete the procedure.</p>
    <p>After the surgical field has been prepared, the duct at the neck of the gallbladder, known as the cystic duct, which normally allows drainage of secretions from the gallbladder to your gut, is clamped and cut. This same process will occur for the neighboring blood vessel, known as the cystic artery. The gallbladder will be delicately separated from the liver. The gallbladder is now free and will be taken out from your belly through a one of the tiny incisions.</p>
    <p>Your surgeon will make sure everything looks good inside your belly before closing your four incisions with suture or staples and applying dressings over them. The procedure typically takes less than 2 hours.</p>
    <p>You will wake up in the operating room and be transported to the capable hands of the nursing staff in the post-anesthesia care unit, commonly referred to as the PACU. Once you have started to recover from the effects of the general anesthetic, a friend or family member may come stay with you.</p>
  </div>

  <div class="accordion" style="top:946px"><span class="accordion__label">Immediately after</span><span class="accordion__toggle">+</span></div>

  <nav class="nav" aria-label="App navigation">
    <svg style="left:17px" width="16" height="16" viewBox="0 0 16 16"><path d="M1 8 L8 2 L15 8 L13 8 L13 14 L9.5 14 L9.5 10 L6.5 10 L6.5 14 L3 14 L3 8 Z" fill="#fff"/></svg>
    <svg style="left:61px" width="16" height="16" viewBox="0 0 16 16" fill="var(--nav-icon)"><circle cx="8" cy="5" r="2.6"/><circle cx="3" cy="6" r="2"/><circle cx="13" cy="6" r="2"/><path d="M3 14 Q3 8.5 8 8.5 Q13 8.5 13 14 Z"/><path d="M0 13 Q0 9 3 9 L4 9 Q2.5 11 2.5 13 Z M16 13 Q16 9 13 9 L12 9 Q13.5 11 13.5 13 Z"/></svg>
    <svg style="left:103px" width="16" height="16" viewBox="0 0 16 16"><circle cx="8" cy="8" r="7" fill="none" stroke="var(--nav-icon)" stroke-width="1.6"/><path d="M11.5 8 H5 M7.5 5 L4.5 8 L7.5 11" fill="none" stroke="var(--nav-icon)" stroke-width="1.8"/></svg>
    <svg style="left:145px" width="16" height="16" viewBox="0 0 16 16"><circle cx="8" cy="8" r="7" fill="none" stroke="var(--nav-icon)" stroke-width="1.6"/><path d="M4.5 8 H11 M8.5 5 L11.5 8 L8.5 11" fill="none" stroke="var(--nav-icon)" stroke-width="1.8"/></svg>
    <svg style="left:188px" width="16" height="16" viewBox="0 0 16 16"><circle cx="8" cy="8" r="5" fill="none" stroke="var(--nav-icon)" stroke-width="3" stroke-dasharray="2.2 1.7"/><circle cx="8" cy="8" r="4" fill="var(--nav-icon)"/><circle cx="8" cy="8" r="1.6" fill="var(--nav)"/></svg>
  </nav>
</section>

</body>
</html>
```